I need a business card designed using the logo provided either vertical or horizontal......Harbourline Property Group is an Australian based real estate company that caters for the upper end of the market so the design of the business card "must reflect" the companies image!!
Colour combinations are optional but "must be realistic" and must be able to be accurately useable CMYK colours.
Please consider that any colours used "must be able to be used" and be suitable in following designs for "pull out banner signs" and "real estate signs".
The colours and the font in the attached designs are for example and other combinations are encouraged.
Target Market(s)
The High End of the Australian real estate market
Industry/Entity Type
Business
Contact Information for Business Card
Logo - Business Name - Director + Licensed Real Estate Agent - Mobile Number (Cell Phone) - Business Number - Fax - Email Address - Web address
Requirements
Must have
- Designs and colours (CMYK) that can easily be interpreted by an Australian printer.
Nice to have
- Some alternative ideas on colour and font..........the ones provided are ok and have been provided as an example but I am looking for alternative ideas
Should not have
- Loud, overly bright colours. Designs that do not reflect the professional standards of the business.
- Designs that look good on a computer monitor but can not be re-created on a printing press.............this is most important when it comes to shading etc.

```html
<!DOCTYPE html>
<html lang="en">
<head>
<meta charset="utf-8">
<title>Harbourline Property Group – Business Card</title>
<link rel="stylesheet" href="https://fonts.googleapis.com/css2?family=Lato:wght@400;700&display=swap">
<style>
  :root {
    --page: #3a3533;
    --card-back: #0c0c0c;
    --card-front: #242426;
    --gold: #c8923c;
    --cream: #ece3c9;
    --soft-white: #d9d6cf;
    --ghost: #1d1d1d;
  }
  * { box-sizing: border-box; margin: 0; padding: 0; }
  html, body {
    width: 1200px;
    height: 844px;
    overflow: hidden;
    background: var(--page);
    font-family: "Lato", sans-serif;
  }
  .stage {
    position: relative;
    width: 1200px;
    height: 844px;
  }
  .card {
    position: absolute;
    top: 272px;
    width: 525px;
    height: 300px;
    border-radius: 3px;
    overflow: hidden;
  }
  /* contact side */
  .card--contact {
    left: 50px;
    background: var(--card-back);
  }
  .card__ghost-mark {
    position: absolute;
    left: 30px;
    top: 70px;
    width: 210px;
    height: 210px;
  }
  .card__person {
    position: absolute;
    left: 196px;
    top: 52px;
  }
  .card__name {
    font-weight: 700;
    font-size: 19px;
    letter-spacing: 0.06em;
    color: var(--cream);
    padding-bottom: 4px;
    border-bottom: 1px solid var(--gold);
  }
  .card__role {
    margin-top: 5px;
    padding-left: 26px;
    font-size: 15px;
    color: var(--gold);
  }
  .card__details {
    position: absolute;
    right: 150px;
    top: 140px;
    list-style: none;
    text-align: right;
    font-size: 15px;
    line-height: 1.35;
    color: var(--gold);
  }
  .card__address {
    position: absolute;
    left: 196px;
    bottom: 30px;
    font-size: 14px;
    color: var(--soft-white);
    white-space: nowrap;
  }
  /* logo side */
  .card--brand {
    left: 625px;
    background: var(--card-front);
    display: flex;
    align-items: center;
    justify-content: center;
  }
  .brand {
    display: flex;
    align-items: center;
    gap: 14px;
  }
  .brand__dot {
    width: 16px;
    height: 16px;
    background: var(--cream);
  }
  .brand__name {
    font-weight: 700;
    font-size: 24px;
    letter-spacing: 0.08em;
    text-transform: uppercase;
    color: var(--cream);
    line-height: 1.25;
  }
</style>
</head>
<body>
  <main class="stage">
    <section class="card card--contact" aria-label="Business card, contact side">
      <svg class="card__ghost-mark" viewBox="0 0 210 210" aria-hidden="true">
        <circle cx="105" cy="105" r="100" fill="var(--ghost)"/>
      </svg>
      <div class="card__person">
        <p class="card__name">DANIEL WHITFORD</p>
        <p class="card__role">Managing Director</p>
      </div>
      <ul class="card__details">
        <li>0412-583-706</li>
        <li>02-9417-3280</li>
        <li>daniel@harbourlinepg.com.au</li>
        <li>www.harbourlinepg.com.au</li>
      </ul>
      <p class="card__address">58 Wharf Terrace | Mosman, NSW | 2088</p>
    </section>

    <section class="card card--brand" aria-label="Business card, brand side">
      <div class="brand">
        <span class="brand__dot" aria-hidden="true"></span>
        <p class="brand__name">Harbourline<br>Property Group</p>
      </div>
    </section>
  </main>
</body>
</html>
```